Redesign Comparisson chart - make modern and effective

Use your imaginations to make a powerful distinction between KMV & other holistic modalities. There are 7 elements physical, mental, emotional, energetic, subconscious, superconscious and before and after testing.
We want it to be obvious that KMV is the only modality that works on all these elements simultaneously. We do not want to include any chakras as we want this information to be accepted by a wide range of people and belief systems.'

We want it to look simple but effective. Professional but powerful. We want KMV to stand out even of you eye just passed over i.
Updates

Hi everyone, thanks for your submissions so far. Basically what this image is meant to represent is a comparison chart between all the modalities There are 5 elements physical, mental, emotional, subconscious and superconscious. we want to reflect that KMV is the only modality that works on all these elements simultaneously. As we want the concept to be accepted and not considered woo woo, we want to steer away from chakras.

Target Market(s)

Professionals

Industry/Entity Type

Professional services

Font styles to use
Sans Serif
Other font styles liked:
• Poppins Monserratt

Colors
0094D4
00A9DD
6FCCEA
C7EBF8
E9F6FB

Requirements
Must have
• Clear/professional and clean look. Brand colours and logos. All typography and formats must be cohesive.
Nice to have
• More easy to read, different layout
Should not have
• Do not change the data just the way its presented. No chakras

```html
<!DOCTYPE html>
<html lang="en">
<head>
<meta charset="utf-8">
<title>KMV – Modality Comparison Chart</title>
<link href="https://fonts.googleapis.com/css2?family=Poppins:ital,wght@0,400;0,500;0,600;1,600&display=swap" rel="stylesheet">
<style>
  :root{
    --brand:#2fb6e6;
    --brand-strong:#0094d4;
    --ink:#1d5a6e;
    --text:#1b1b1b;
    --bg:#eef2fa;
    --tube:#e2e5ec;
    --red:#dc4a40;
    --blue:#62bedd;
    --orange:#f2a035;
    --yellow:#e9d150;
    --pink:#d475ad;
    --purple:#836dae;
    --green:#5fad45;
    --tick:#7dd6f7;
  }
  *{margin:0;padding:0;box-sizing:border-box}
  html,body{width:1200px;height:825px;overflow:hidden;background:#fff}
  body{font-family:'Poppins',sans-serif;position:relative}
  .chart-bg{position:absolute;left:0;top:109px;width:1200px;height:716px;background:var(--bg)}
  .chart{position:absolute;left:0;top:0;width:1200px;height:825px}
  .abs{position:absolute}

  .headline{left:73px;top:36px;font-size:20.5px;line-height:23.5px;font-weight:600;color:var(--brand);letter-spacing:.3px}
  .brand-mark{left:1122px;top:0}
  .brand-name{left:580px;top:34px;font-size:30px;font-weight:600;color:var(--brand);line-height:36px}
  .manifesto{left:690px;top:33px;width:486px;text-align:center;font-size:8.4px;line-height:13.2px;font-style:italic;font-weight:600;color:var(--text)}

  .modality{list-style:none;font-size:10.4px;line-height:13.5px;font-weight:600;color:var(--ink);letter-spacing:.3px}
  .modality li{padding-left:8px;position:relative;white-space:nowrap}
  .modality li::before{content:"";position:absolute;left:0;top:5px;width:4px;height:4px;border-radius:50%;background:var(--ink)}

  .element h2{font-size:14.4px;line-height:16.8px;font-weight:600;letter-spacing:.3px}
  .element p{font-size:8px;line-height:9.6px;color:var(--text);text-align:justify;margin-top:1px}
  .element.left{text-align:right}
  .element.left p{text-align-last:left}
  .element{width:136px}
  .testing h2{color:var(--pink)}
  .superconscious h2{color:var(--purple)}
  .subconscious h2{color:var(--yellow)}
  .energetic h2{color:var(--orange)}
  .emotional h2{color:var(--green)}
  .mental h2{color:var(--blue)}
  .physical h2{color:var(--red)}

  .footer-brand{left:517px;top:786px;font-size:13px;font-weight:600;color:var(--brand);display:flex;align-items:center;gap:10px}
  .footer-brand .dot{width:14px;height:14px;border-radius:50%;background:var(--brand)}
  .footer-brand .sep{width:1px;height:16px;background:var(--brand)}
  .footer-brand .url{font-weight:500;font-size:11px}
</style>
</head>
<body>
  <div class="chart-bg"></div>

  <svg class="chart" viewBox="0 0 2322 1596" aria-hidden="true">
    <defs>
      <g id="tube-top"><rect x="-21" y="372" width="42" height="380" rx="21" fill="var(--tube)"/></g>
      <g id="tube-bottom"><rect x="-21" y="1053" width="42" height="380" rx="21" fill="var(--tube)"/></g>
    </defs>

    <!-- header brand circle -->
    <circle cx="1061" cy="102" r="47" fill="var(--brand)"/>

    <!-- connectors -->
    <g stroke="var(--ink)" stroke-width="3" fill="none">
      <path d="M284 321H474M379 321V400M530 321H720M625 321V400"/>
      <path d="M135 780H354M256 702V780M408 780H598M502 702V780"/>
      <path d="M1757 321H1947M1852 321V400M2018 321H2178M2098 321V400"/>
      <path d="M1648 780H1810M1728 702V780M1880 780H2070M1975 702V780"/>
      <path d="M284 1003H474M379 1003V1081M559 1003H691M625 1003V1081"/>
      <path d="M147 1461H366M256 1383V1461M422 1461H583M502 1383V1461"/>
      <path d="M1648 1003H1810M1728 1003V1081M1866 1003H2085M1975 1003V1081"/>
      <path d="M1772 1461H1932M1852 1383V1461M2013 1461H2175M2098 1383V1461"/>
      <path d="M1022 1478H1300"/>
    </g>

    <!-- top-left tubes -->
    <g transform="translate(256 0)"><use href="#tube-top"/><rect x="-21" y="677" width="42" height="55" fill="var(--red)"/><circle cy="731" r="21" fill="var(--red)"/></g>
    <g transform="translate(379 0)"><use href="#tube-top"/><rect x="-21" y="592" width="42" height="76" fill="var(--blue)"/><rect x="-21" y="677" width="42" height="55" fill="var(--red)"/><circle cy="731" r="21" fill="var(--red)"/></g>
    <g transform="translate(502 0)"><use href="#tube-top"/><rect x="-21" y="508" width="42" height="76" fill="var(--orange)"/><rect x="-21" y="592" width="42" height="76" fill="var(--blue)"/><rect x="-21" y="677" width="42" height="55" fill="var(--red)"/><circle cy="731" r="21" fill="var(--red)"/></g>
    <g transform="translate(625 0)"><use href="#tube-top"/><rect x="-21" y="592" width="42" height="76" fill="var(--orange)"/><rect x="-21" y="677" width="42" height="55" fill="var(--red)"/><circle cy="731" r="21" fill="var(--red)"/></g>

    <!-- top-right tubes -->
    <g transform="translate(1728 0)"><use href="#tube-top"/><rect x="-21" y="423" width="42" height="76" fill="var(--pink)"/><rect x="-21" y="508" width="42" height="76" fill="var(--yellow)"/><rect x="-21" y="592" width="42" height="76" fill="var(--orange)"/><rect x="-21" y="677" width="42" height="55" fill="var(--red)"/><circle cy="731" r="21" fill="var(--red)"/></g>
    <g transform="translate(1852 0)"><use href="#tube-top"/><rect x="-21" y="677" width="42" height="55" fill="var(--orange)"/><circle cy="731" r="21" fill="var(--orange)"/></g>
    <g transform="translate(1975 0)"><use href="#tube-top"/><rect x="-21" y="592" width="42" height="76" fill="var(--pink)"/><rect x="-21" y="677" width="42" height="55" fill="var(--orange)"/><circle cy="731" r="21" fill="var(--orange)"/></g>
    <g transform="translate(2098 0)"><use href="#tube-top"/><rect x="-21" y="592" width="42" height="76" fill="var(--purple)"/><rect x="-21" y="677" width="42" height="55" fill="var(--yellow)"/><circle cy="731" r="21" fill="var(--yellow)"/></g>

    <!-- bottom-left tubes -->
    <g transform="translate(256 0)"><use href="#tube-bottom"/><rect x="-21" y="1273" width="42" height="76" fill="var(--pink)"/><rect x="-21" y="1358" width="42" height="55" fill="var(--red)"/><circle cy="1412" r="21" fill="var(--red)"/></g>
    <g transform="translate(379 0)"><use href="#tube-bottom"/><rect x="-21" y="1189" width="42" height="76" fill="var(--pink)"/><rect x="-21" y="1273" width="42" height="76" fill="var(--orange)"/><rect x="-21" y="1358" width="42" height="55" fill="var(--red)"/><circle cy="1412" r="21" fill="var(--red)"/></g>
    <g transform="translate(502 0)"><use href="#tube-bottom"/><rect x="-21" y="1189" width="42" height="76" fill="var(--pink)"/><rect x="-21" y="1273" width="42" height="76" fill="var(--yellow)"/><rect x="-21" y="1358" width="42" height="55" fill="var(--red)"/><circle cy="1412" r="21" fill="var(--red)"/></g>
    <g transform="translate(625 0)"><use href="#tube-bottom"/><rect x="-21" y="1104" width="42" height="76" fill="var(--pink)"/><rect x="-21" y="1189" width="42" height="76" fill="var(--yellow)"/><rect x="-21" y="1273" width="42" height="76" fill="var(--blue)"/><rect x="-21" y="1358" width="42" height="55" fill="var(--red)"/><circle cy="1412" r="21" fill="var(--red)"/></g>

    <!-- bottom-right tubes -->
    <g transform="translate(1728 0)"><use href="#tube-bottom"/><rect x="-21" y="1358" width="42" height="55" fill="var(--blue)"/><circle cy="1412" r="21" fill="var(--blue)"/></g>
    <g transform="translate(1852 0)"><use href="#tube-bottom"/><rect x="-21" y="1273" width="42" height="76" fill="var(--pink)"/><rect x="-21" y="1358" width="42" height="55" fill="var(--blue)"/><circle cy="1412" r="21" fill="var(--blue)"/></g>
    <g transform="translate(1975 0)"><use href="#tube-bottom"/><rect x="-21" y="1273" width="42" height="76" fill="var(--yellow)"/><rect x="-21" y="1358" width="42" height="55" fill="var(--blue)"/><circle cy="1412" r="21" fill="var(--blue)"/></g>
    <g transform="translate(2098 0)"><use href="#tube-bottom"/><rect x="-21" y="1189" width="42" height="76" fill="var(--pink)"/><rect x="-21" y="1273" width="42" height="76" fill="var(--yellow)"/><rect x="-21" y="1358" width="42" height="55" fill="var(--blue)"/><circle cy="1412" r="21" fill="var(--blue)"/></g>

    <!-- connector dots -->
    <g fill="var(--ink)">
      <circle cx="379" cy="400" r="6"/><circle cx="625" cy="400" r="6"/><circle cx="256" cy="702" r="6"/><circle cx="502" cy="702" r="6"/>
      <circle cx="1852" cy="400" r="6"/><circle cx="2098" cy="400" r="6"/><circle cx="1728" cy="702" r="6"/><circle cx="1975" cy="702" r="6"/>
      <circle cx="379" cy="1081" r="6"/><circle cx="625" cy="1081" r="6"/><circle cx="256" cy="1383" r="6"/><circle cx="502" cy="1383" r="6"/>
      <circle cx="1728" cy="1081" r="6"/><circle cx="1975" cy="1081" r="6"/><circle cx="1852" cy="1383" r="6"/><circle cx="2098" cy="1383" r="6"/>
    </g>

    <!-- central KMV tube -->
    <g>
      <rect x="1137" y="253" width="50" height="1057" rx="25" fill="var(--tube)"/>
      <rect x="1137" y="338" width="50" height="118" fill="var(--pink)"/>
      <rect x="1137" y="338" width="50" height="20" rx="10" fill="#b85892"/>
      <rect x="1137" y="466" width="50" height="132" fill="var(--purple)"/>
      <rect x="1137" y="609" width="50" height="132" fill="var(--yellow)"/>
      <rect x="1137" y="751" width="50" height="132" fill="var(--orange)"/>
      <rect x="1137" y="893" width="50" height="132" fill="var(--green)"/>
      <rect x="1137" y="1035" width="50" height="132" fill="var(--blue)"/>
      <rect x="1137" y="1177" width="50" height="108" fill="var(--red)"/>
      <circle cx="1162" cy="1285" r="25" fill="var(--red)"/>
      <circle cx="1162" cy="313" r="37" fill="var(--tick)"/>
      <path d="M1144 314l12 12 22-24" stroke="#fff" stroke-width="8" fill="none" stroke-linecap="round" stroke-linejoin="round"/>
      <path d="M1162 1262V1352" stroke="var(--ink)" stroke-width="3"/>
      <circle cx="1162" cy="1262" r="6" fill="var(--ink)"/>
      <circle cx="1162" cy="1410" r="60" fill="var(--brand)"/>
    </g>

    <!-- element connectors -->
    <g stroke-width="2" fill="none">
      <path d="M1218 326V450M1187 380H1218" stroke="var(--pink)"/>
      <path d="M1104 470V595M1104 520H1137" stroke="var(--purple)"/>
      <path d="M1218 610V745M1187 660H1218" stroke="var(--yellow)"/>
      <path d="M1104 757V880M1104 805H1137" stroke="var(--orange)"/>
      <path d="M1218 870V1025M1187 948H1218" stroke="var(--green)"/>
      <path d="M1104 1040V1162M1104 1088H1137" stroke="var(--blue)"/>
      <path d="M1218 1137V1300M1187 1222H1218" stroke="var(--red)"/>
    </g>
  </svg>

  <!-- header -->
  <h1 class="abs headline">CHOOSE KMV FOR FAST, IMMEDIATE AND<br>POWERFUL RESULTS</h1>
  <div class="abs brand-name">KMV</div>
  <p class="abs manifesto">I MUST EXPERIENCE HEALING ON ALL LEVELS, I AM NOT JUST A BODY.<br>I WANT TO LEARN HOW TO HEAL MYSELF, SO I'M NOT DEPENDENT ON OTHERS.<br>I WANT TO RELEASE ALL MY EMOTIONAL AND MENTAL BLOCKS, SO I CAN BE THE BEST VERSION OF MYSELF.</p>

  <!-- modalities -->
  <ul class="abs modality" style="left:149px;top:151px"><li>PSYCHIC INTUITIVE</li></ul>
  <ul class="abs modality" style="left:276px;top:151px"><li>ACUPUNCTURE</li></ul>
  <ul class="abs modality" style="left:71px;top:409px"><li>MASSAGE</li><li>YOGA</li><li>NATROPATHY</li><li>AYURVEDIC MEDICINE</li><li>WESTERN MEDICINE</li></ul>
  <ul class="abs modality" style="left:212px;top:409px"><li>FAMILY<br>CONSTELLATION</li></ul>

  <ul class="abs modality" style="left:910px;top:137px"><li>REIKI</li><li>CRYSTAL HEALING</li></ul>
  <ul class="abs modality" style="left:1044px;top:151px"><li>THETA HEALING</li></ul>
  <ul class="abs modality" style="left:854px;top:409px"><li>CHIROPRACTIC</li></ul>
  <ul class="abs modality" style="left:974px;top:409px"><li>ENERGY MEDICINE</li></ul>

  <ul class="abs modality" style="left:149px;top:503px"><li>CHINESE MEDICINE</li></ul>
  <ul class="abs modality" style="left:291px;top:503px"><li>EFT</li></ul>
  <ul class="abs modality" style="left:78px;top:761px"><li>NUTRITIONAL<br>HEALING</li></ul>
  <ul class="abs modality" style="left:220px;top:761px"><li>KINESIOLOGY</li><li>BOWEN THERAPY</li></ul>

  <ul class="abs modality" style="left:854px;top:503px"><li>PSYCHOLOGY</li></ul>
  <ul class="abs modality" style="left:966px;top:476px"><li>HYPNOTHERAPY</li><li>INNER CHILD<br>HEALING</li></ul>
  <ul class="abs modality" style="left:918px;top:761px"><li>MINDFULNESS<br>MEDITATION</li><li>LIFE COACHING</li></ul>
  <ul class="abs modality" style="left:1042px;top:761px"><li>NLP</li><li>TIMELINE THERAPY</li></ul>

  <ul class="abs modality" style="left:530px;top:770px"><li>KINETIC MIND VITALITY</li></ul>

  <!-- elements -->
  <section class="abs element testing" style="left:636px;top:166px">
    <h2>BEFORE &amp; AFTER<br>TESTING</h2>
    <p>KMV is the only modality the enables you to provide before and after results, which are documented by us, and analysed by you with our help.</p>
  </section>
  <section class="abs element left superconscious" style="left:427px;top:240px">
    <h2>SUPERCONSCIOUS</h2>
    <p>KMV is the only modality the enables you to access and heal your superconscious mind yourself.</p>
  </section>
  <section class="abs element subconscious" style="left:636px;top:313px">
    <h2>SUBCONSCIOUS</h2>
    <p>Some modalities, like Kinesiology, access your subconscious through muscle testing.<br>KMV empowers you to access your own subconscious and heal it yourself.</p>
  </section>
  <section class="abs element left energetic" style="left:427px;top:389px">
    <h2>ENERGETIC</h2>
    <p>Most modalities try to move the energy in your body for you. KMV enables and empowers you to do it yourself.</p>
  </section>
  <section class="abs element emotional" style="left:636px;top:448px">
    <h2>EMOTIONAL</h2>
    <p>KMV is the only modality that engages your emotions on a physical level. Emotions get stuck in your body and can cause illness over time if left unchecked. KMV enables you you experience fast and powerful emotional releasing</p>
  </section>
  <section class="abs element left mental" style="left:427px;top:535px">
    <h2>MENTAL</h2>
    <p>KMV enables you to use your own consciousness to self-heal. We don't give you advice or coaching, we allow your mind to heal itself.</p>
  </section>
  <section class="abs element physical" style="left:636px;top:585px">
    <h2>PHYSICAL</h2>
    <p>Most modalities, including, a western medicine, focus on and treat the physical body only. The KMV process enables you to engage in healing your own body during the session. There is no muscle testing, no hands-on healing and no herbal remedies or medicines.</p>
  </section>

  <!-- footer -->
  <div class="abs footer-brand"><span class="dot"></span><span>Brightmend</span><span class="sep"></span><span class="url">www.brightmend.com.au</span></div>
</body>
</html>
```